The Korvessel Bands: Vesperance Paranormal Romance Cover Contest

Adult paranormal romance cover & e-cover (jpeg longest side not to exceed 2500 pixels, 1600 x 2500 uploads fine), 72 dpi, RGB. Plus, paperback pdf with back approximately 254 pages, .64 spine (16.26 mm), 300dpi, bleed .5, size 5.5 x 8.5. leave room for ISBN on back bottom right. Books 1 and 2 of series (The Korvessel Bands: Lantern/ & Harborlight) are on Brindlecart.example. Author name L. M. Garrow, for reference. New font will need to be selected. For book 3 Vesperance, I am hoping for an inverted Egyptian pyramid, prefer nighttime because that is when they will break into the Giza in order to find Isis's hidden amber amulet. The title Vesperance happens because the main character can see the secret inverted doorway inside the Giza that accesses Isis's hidden room. The main character's (Mabel & Corvin) will have a tattoo magically created on them (heart area) during the immortal ceremony. The tattoo is planned as an inverted pyramid with the arabic symbol/word for Hidden on top of (or could use a simple triangle whatever works best). If a human element is needed Mabel has light brown hair, multi-tonal, and blue-green eyes, wears ponytails a lot almost age 17, her soon to be immortal mate Corvin De Lacey (actor Brent Lomaski was my inspiration for the look of the character include snapshot as reference only) is desperately trying to prevent Mabel from dying and becoming a portal (she gets engulfed in bright light floating off her bed in one scene another scene the light glows behind her eyes). The tattoo also has ribbons of amber weaved in it symbolic of the amulet they are searching for. Isis's amulet will let her control the portal so she can live. The overall series is about a team of 8 immortal guardians that are each fated for one person if their magical ring doesn't find them then they might turn into the evil they are protecting mankind from. The first half of the book is set in Salem, MA there is a scene with Spirovo board that tells them to find the amulet and go to Egypt or die (another idea for cover is the eye from the Spirovo board maybe over a map of Egypt.) Before breaking into the Giza they trek through the desert with a team to a Sunken Obelisk to get clues. The Sunken Obelisk is buried in sand and they magically move the sand to access it. I have uploaded a snapshot from pixel vault that reminds me of Mabel especially her eyes, but I have not purchased any of the snapshots. Also included Arabic word for hidden. Any photos used will have to have basic rights to the photo. My author pic is upload black and white with glasses and pdf of back summary. Hope I've included enough info. Thanks, L. M. Garrow
Open to artistic ideas.

ADDING INFORMATION 9/14: All of the above is correct. A few additional comments in general but are not in anyway needed to be added. Everyone's work is awesome! The series is based in 2023. All of the immortals (7 guys, 1 women are bad to the bone warriors - there is nothing soft about them and killing is what they do best but times have changed and they are more refined and blend into society.) Book 3 Vesperance is Corvin's story he is the super brains, super hot ladies' man of the group and he goes undercover at Salem, MA high school where at first he doesn't know it but he meets his mate Mabel - she's a nobody under baggy clothes. Corvin will need to help save Mabel or she dies. Their big mission is to go to Egypt to get Isis's amulet after they play jokingly Spirovo board with friends at Crowfeather Hollow that talks directly to Mabel. Mabel is changing into a portal. The amulet is the only way for her to not die and be able to control the portal. Part of her changing is that her vision is changing hence I called the book Vesperance because she is seeing things inverted or that others aren't able to see without the help of magical glasses. So they go to the Sunken Obelisk and use magic to gain entrance looking for clues which they get then they break into the Giza at night for the grand finale. The immortal ceremony happens inside the Giza where the leader strikes lightning into Mabel's heart and at that moment The Korvessel Band (looks ancient/viking like) (each immortal has) divides identically for the chosen mate and a tattoo is engraved over their heart. Each immortal has a different symbol one that represents the couple. Though I can modify how I wrote it based on designs, at present it is an inverted triangle or pyramid with amber ribbons and the arabic word/symbol for hidden. One other element that does come up in the novel is the magical tropical yellow flower from the deadly Karakoram Mountain, that they had to get first to help save her. It has healing powers. When the flower is still in bloom it is just waved/touched and it heals. As it dies super smart Corvin crushes it up and has Mabel drink the petals. Well I hope the extra comments helped. As soon as I figure out how to put designers in my like pile I will be excited to have you work on future projects. The series has 8 total planned with a spin off series for their kids. Also all the adult books are also being modified for young adult. That's a lot of covers. So thank you all for such great submissions. Sorry I haven't used the star rating yet but I'm not sure I like what the stars represent. As we come into the final days I will mark off the stars. Thanks again for all the hard work.

Target Market(s)

Primarily Women 18+

Industry/Entity Type

Adult

Font styles to use
Serif
Script

Requirements
Nice to have
• Open on font style. Open on colors though main characters eyes are emphasized in book blue-green and are referred to as color of an Ammolite gem. The only other main colors are the bright light of the portal and Isis's amber amulet.

```html
<!DOCTYPE html>
<html lang="en">
<head>
<meta charset="utf-8">
<title>The Korvessel Band: Vesperance — Back Cover</title>
<link rel="stylesheet" href="https://fonts.googleapis.com/css2?family=Cinzel+Decorative:wght@700&family=Cinzel:wght@400;600&family=Libre+Baskerville:ital,wght@0,400;0,700;1,400&family=Great+Vibes&display=swap">
<style>
  :root {
    --bg-deep: #2a0410;
    --bg-mid: #6e0c28;
    --bg-glow: #b0204a;
    --title-teal: #6fe3f0;
    --title-pale: #e9fbff;
    --subtitle-grey: #d6d3dc;
    --tagline-gold: #ffe34a;
    --body-white: #ffffff;
    --rule: rgba(255, 255, 255, 0.55);
    --photo-tone: #8a8a8a;
  }
  * { margin: 0; padding: 0; box-sizing: border-box; }
  html, body { width: 769px; height: 1200px; overflow: hidden; background: var(--bg-deep); }
  .back-cover {
    position: relative;
    width: 769px;
    height: 1200px;
    overflow: hidden;
    background:
      radial-gradient(circle at 12% 18%, rgba(255, 90, 140, 0.35) 0 40px, transparent 70px),
      radial-gradient(circle at 88% 10%, rgba(255, 120, 160, 0.3) 0 55px, transparent 90px),
      radial-gradient(circle at 8% 62%, rgba(220, 60, 110, 0.3) 0 60px, transparent 100px),
      radial-gradient(circle at 92% 55%, rgba(230, 80, 120, 0.28) 0 50px, transparent 90px),
      radial-gradient(circle at 15% 92%, rgba(255, 110, 150, 0.3) 0 45px, transparent 80px),
      radial-gradient(circle at 85% 90%, rgba(240, 90, 130, 0.3) 0 60px, transparent 100px),
      radial-gradient(ellipse at 50% 45%, var(--bg-glow) 0%, var(--bg-mid) 45%, var(--bg-deep) 100%);
  }
  .series-title {
    position: absolute;
    top: 20px; left: 0; width: 100%;
    text-align: center;
    font-family: "Cinzel Decorative", serif;
    font-weight: 700;
    font-size: 50px;
    color: var(--title-teal);
    text-shadow: 0 0 6px rgba(0,0,0,0.6), 0 2px 0 var(--title-pale);
    letter-spacing: 1px;
  }
  .survives {
    position: absolute;
    top: 86px; left: 0; width: 100%;
    text-align: center;
    font-family: "Cinzel", serif;
    font-size: 15px;
    letter-spacing: 9px;
    color: var(--subtitle-grey);
  }
  .book-title {
    position: absolute;
    top: 98px; left: 0; width: 100%;
    text-align: center;
    font-family: "Cinzel", serif;
    font-weight: 600;
    font-size: 44px;
    color: var(--subtitle-grey);
    text-shadow: 0 2px 4px rgba(0,0,0,0.6);
  }
  .tagline {
    position: absolute;
    top: 240px; left: 60px; width: 649px;
    text-align: center;
    font-family: "Libre Baskerville", serif;
    font-size: 23px;
    line-height: 1.45;
    color: var(--tagline-gold);
  }
  .divider {
    position: absolute;
    top: 334px; left: 88px; width: 593px;
    border-top: 1px solid var(--rule);
  }
  .excerpt {
    position: absolute;
    left: 88px; width: 593px;
    font-family: "Libre Baskerville", serif;
    font-style: italic;
    font-size: 17.5px;
    line-height: 1.72;
    color: var(--body-white);
    text-align: justify;
  }
  .excerpt--mabel { top: 352px; }
  .excerpt--corvin { top: 690px; }
  .edition-note {
    position: absolute;
    top: 1030px; left: 60px; width: 649px;
    text-align: center;
    font-family: "Cinzel", serif;
    font-size: 12px;
    letter-spacing: 0.5px;
    color: var(--tagline-gold);
  }
  .author-photo {
    position: absolute;
    top: 1056px; left: 318px; width: 134px; height: 116px;
    border-radius: 50% 50% 8px 8px / 40% 40% 8px 8px;
    background: radial-gradient(circle at 50% 40%, #bdbdbd, var(--photo-tone) 60%, #3a3a3a);
  }
  .author-name {
    position: absolute;
    top: 1130px; left: 0; width: 100%;
    text-align: center;
    font-family: "Great Vibes", cursive;
    font-size: 48px;
    color: var(--body-white);
    text-shadow: 0 2px 4px rgba(0,0,0,0.7);
  }
</style>
</head>
<body>
<main class="back-cover">
  <h1 class="series-title">The Korvessel Band</h1>
  <p class="survives">SURVIVES</p>
  <p class="book-title">Vesperance</p>

  <p class="tagline">Time is running out to save Mabel, and Corvin will stop at nothing to make sure she survives the vesperance.</p>
  <div class="divider"></div>

  <p class="excerpt excerpt--mabel">~ Mabel ~ Geez, that stupid jock tripped me again. I patted the hallway floor of Salem High searching for my glasses. A pair of tennis shoes appeared in my blurred vision. I stole a secretive glance as he offered a very masculine hand to me. Taking hold, I avoided his eyes, because I just knew I’d look like Fennick staring into oncoming traffic. He was that hot. I barely remembered to let go of his hand as I stumbled off in front of him. I think he asked me where his class was. I must have mumbled something, because he’s following me, and now I barely remember where I’m going.</p>

  <p class="excerpt excerpt--corvin">~ Corvin ~ My protective instincts kicked into overdrive when I saw her fall. I hurried over scooping up her glasses while reaching for her hand. The gentle zap took me by surprise as her fingers wrapped over mine. Static electricity — my logic countered, but my stomach clenched in disagreement. I followed her swinging ponytail knowing I just found a friend, and it would appear she was sorely in need of one. Hopefully, she can shed some light on the odd occurrences happening around town. That was why I was here, after all, to destroy any threat to humanity. Hopefully, I will have the problem fixed in no time at all. My stomach gave another tightening at my thought, and I wondered the cause as I studied the petite girl in front of me.</p>

  <p class="edition-note">THE FOLLOWING BOOK IS A REVISED YA EDITION OF THE ADULT TITLE: THE KORVESSEL BANDS: VESPERANCE</p>

  <div class="author-photo" role="img" aria-label="Black and white author portrait with glasses"></div>
  <p class="author-name">L. M. Garrow</p>
</main>
</body>
</html>
```